Create a new business card

I’m looking to update my business card to make it match the rest of my brand. I will include my current website as well as what my vehicle designs look like, etc..
What my business currently services
Weekly maintenance pool openings / closings
Equipment repair, including pumps, heaters, salt systems, filters, etc.
We install automatic covers and maintain them as well as provide preventative maintenance

I would like to include my name.
Dorian Pelkin.
My title
Owner
My email
Dorian@tidewellnx.com
4015827160
Www.tidewellnx.com

```html
<!DOCTYPE html>
<html lang="en">
<head>
<meta charset="utf-8">
<title>Tidewell Pool Care – Business Card</title>
<link rel="stylesheet" href="https://fonts.googleapis.com/css2?family=Poppins:wght@400;500;600;700&display=swap">
<style>
  :root {
    --page-bg: #1a1a1c;
    --navy: #1f2f66;
    --navy-deep: #1c2a5c;
    --sky: #27aae1;
    --orange: #e8651f;
    --white: #ffffff;
    --paper: #f4f4f4;
    --ink: #1f2f66;
    --body-ink: #1c1c24;
  }
  * { box-sizing: border-box; margin: 0; padding: 0; }
  html, body {
    width: 1200px; height: 1122px; overflow: hidden;
    background: var(--page-bg);
    font-family: "Poppins", sans-serif;
  }
  .stage {
    width: 1200px; height: 1122px;
    display: flex; flex-direction: column; align-items: center; justify-content: center;
    gap: 60px;
  }
  .card {
    width: 640px; height: 366px;
    border-radius: 22px;
    display: flex; align-items: center;
    padding: 0 48px 0 44px;
    position: relative;
  }
  .card--front { background: linear-gradient(135deg, var(--navy) 0%, var(--navy-deep) 100%); }
  .card--back { background: radial-gradient(circle at 30% 40%, var(--white) 0%, var(--paper) 100%); }

  .brand {
    width: 250px;
    display: flex; align-items: center; gap: 12px;
  }
  .brand__dot { width: 34px; height: 34px; border-radius: 50%; flex: none; }
  .card--front .brand__dot { background: var(--sky); }
  .card--back .brand__dot { background: var(--sky); }
  .brand__name { font-weight: 600; font-size: 22px; line-height: 1.15; }
  .card--front .brand__name { color: var(--white); }
  .card--back .brand__name { color: var(--navy); }

  .divider {
    width: 2px; height: 150px; background: var(--orange);
    margin: 0 34px 0 22px; flex: none;
  }

  .services__title {
    color: var(--sky); font-weight: 700; font-size: 24px;
    letter-spacing: 1px; text-transform: uppercase; margin-bottom: 6px;
  }
  .services__list { list-style: none; }
  .services__item {
    display: flex; align-items: center; gap: 10px;
    color: var(--white); font-size: 15px; line-height: 25px; letter-spacing: 0.3px;
  }
  .icon { width: 16px; height: 16px; flex: none; }

  .person__name {
    color: var(--ink); font-weight: 700; font-size: 30px;
    letter-spacing: 1.5px; text-transform: uppercase; line-height: 1.1;
  }
  .person__title { color: var(--sky); font-size: 18px; margin-bottom: 10px; }
  .contact { list-style: none; }
  .contact__item {
    display: flex; align-items: center; gap: 12px;
    color: var(--body-ink); font-size: 17px; line-height: 28px;
  }
</style>
</head>
<body>
<main class="stage">

  <section class="card card--front">
    <div class="brand">
      <span class="brand__dot"></span>
      <span class="brand__name">Tidewell Pool Care</span>
    </div>
    <span class="divider"></span>
    <div class="services">
      <h2 class="services__title">Pool Services</h2>
      <ul class="services__list">
        <li class="services__item"><svg class="icon" viewBox="0 0 16 16"><circle cx="8" cy="8" r="8" fill="#27aae1"/><path d="M4.5 8.3l2.3 2.2 4.7-4.8" fill="none" stroke="#1f2f66" stroke-width="2"/></svg>Pool Openings / Closings</li>
        <li class="services__item"><svg class="icon" viewBox="0 0 16 16"><circle cx="8" cy="8" r="8" fill="#27aae1"/><path d="M4.5 8.3l2.3 2.2 4.7-4.8" fill="none" stroke="#1f2f66" stroke-width="2"/></svg>Equipment Repair</li>
        <li class="services__item"><svg class="icon" viewBox="0 0 16 16"><circle cx="8" cy="8" r="8" fill="#27aae1"/><path d="M4.5 8.3l2.3 2.2 4.7-4.8" fill="none" stroke="#1f2f66" stroke-width="2"/></svg>Including Pumps</li>
        <li class="services__item"><svg class="icon" viewBox="0 0 16 16"><circle cx="8" cy="8" r="8" fill="#27aae1"/><path d="M4.5 8.3l2.3 2.2 4.7-4.8" fill="none" stroke="#1f2f66" stroke-width="2"/></svg>Heaters</li>
        <li class="services__item"><svg class="icon" viewBox="0 0 16 16"><circle cx="8" cy="8" r="8" fill="#27aae1"/><path d="M4.5 8.3l2.3 2.2 4.7-4.8" fill="none" stroke="#1f2f66" stroke-width="2"/></svg>Salt Systems</li>
        <li class="services__item"><svg class="icon" viewBox="0 0 16 16"><circle cx="8" cy="8" r="8" fill="#27aae1"/><path d="M4.5 8.3l2.3 2.2 4.7-4.8" fill="none" stroke="#1f2f66" stroke-width="2"/></svg>Filters, etc.</li>
      </ul>
    </div>
  </section>

  <section class="card card--back">
    <div class="brand">
      <span class="brand__dot"></span>
      <span class="brand__name">Tidewell Pool Care</span>
    </div>
    <span class="divider"></span>
    <div class="person">
      <h1 class="person__name">Dorian Pelkin</h1>
      <p class="person__title">Owner</p>
      <ul class="contact">
        <li class="contact__item"><svg class="icon" viewBox="0 0 16 16"><path d="M3.5 1.5l2.5 3-1.5 1.6c.9 2 2.4 3.5 4.4 4.4l1.6-1.5 3 2.5-1.6 2.2C7 13.5 2.5 9 1.5 3.1z" fill="#27aae1"/></svg>4015827160</li>
        <li class="contact__item"><svg class="icon" viewBox="0 0 16 16"><rect x="1" y="3" width="14" height="10" rx="1" fill="#27aae1"/><path d="M1.5 3.8L8 9l6.5-5.2" fill="none" stroke="#fff" stroke-width="1.3"/></svg>Dorian@tidewellnx.com</li>
        <li class="contact__item"><svg class="icon" viewBox="0 0 16 16"><circle cx="8" cy="8" r="7" fill="#27aae1"/><path d="M1 8h14M8 1c-3 3.5-3 10.5 0 14M8 1c3 3.5 3 10.5 0 14" fill="none" stroke="#fff" stroke-width="1"/></svg>tidewellnx.com</li>
      </ul>
    </div>
  </section>

</main>
</body>
</html>
```